Harborview Estates Business Card for Apartment Buildings

Create business cards for resident managers who run apartment buildings. The audience is the public who are searching for apartment rentals, and current residents who live at the apartment building. Key design element will be incorporating the company logo, however, the logo cannot dominate. The building name and manager name are more important than the logo. Current business card design leaves little room for copy, so we may need to reduce the size on the current card to allow for more space for copy.

Target Market(s)

Adults 18-65 years of age, who are looking for an apartment rental, plus current residents who live at our apartment buildings.

Industry/Entity Type

Property Management

Contact Information for Business Card

A major design element will be use of the company logo. Important property and manager contact information must be part of the design. The size of the logo will need to be reduced to make room for building and manager contact copy.

Font styles to use
Sans Serif

Colors
3176b5
000000
959595
ffffff

Requirements
Must have
• 1) Incorporate the company logo.
• 2) Use the company colors (dark blue, black/grey, over white).
• 3) FEATURE THE BUILDING NAME
• 4) FEATURE THE MANAGER NAME
• 5) The company name is less important than BUILDING and MANAGER
• 6) Manager contact information
• **SEE ATTACHED CREATIVE BRIEF**
Nice to have
• 1) Back of card logo watermark
• 2) Ability to write notes on back of carfd
Should not have
• Avoid letting the company logo dominate the card, the building name and manager are more important than the company logo.

```html
<!DOCTYPE html>
<html lang="en">
<head>
<meta charset="utf-8">
<title>Harborview Estates Business Card</title>
<link rel="stylesheet" href="https://fonts.googleapis.com/css2?family=Arimo:wght@400;700&display=swap">
<style>
  :root {
    --brand-blue: #1d5c9c;
    --ink: #111111;
    --grey: #959595;
    --paper: #ffffff;
    --backdrop: #e9eaec;
  }
  * { box-sizing: border-box; margin: 0; padding: 0; }
  html, body { width: 1200px; height: 800px; overflow: hidden; }
  body {
    background: var(--backdrop);
    font-family: "Arimo", Arial, sans-serif;
    display: flex;
    align-items: center;
    justify-content: center;
    gap: 40px;
  }
  .card {
    position: relative;
    width: 540px;
    height: 309px;
    background: var(--paper);
    box-shadow: 0 8px 24px rgba(0,0,0,0.18);
    overflow: hidden;
  }

  /* front */
  .front-tab {
    position: absolute;
    left: 0; top: 20px;
    width: 70px; height: 118px;
    background: var(--brand-blue);
  }
  .front-brand {
    position: absolute;
    left: 34px; top: 48px;
    display: flex; align-items: center; gap: 12px;
  }
  .brand-square {
    width: 46px; height: 46px;
    background: var(--brand-blue);
    border: 3px solid var(--paper);
  }
  .brand-name {
    color: var(--brand-blue);
    font-weight: 700;
    font-size: 30px;
    line-height: 1;
    letter-spacing: 0.5px;
    text-transform: uppercase;
  }
  .brand-sub {
    display: block;
    font-size: 13px;
    letter-spacing: 3px;
    margin-top: 5px;
  }
  .address {
    position: absolute;
    right: 26px; top: 108px;
    text-align: right;
    font-size: 11.5px;
    line-height: 1.35;
    color: var(--ink);
  }
  .address .web { color: var(--brand-blue); }
  .rule {
    position: absolute;
    left: 28px; right: 26px; top: 172px;
    height: 1.5px;
    background: var(--brand-blue);
  }
  .manager {
    position: absolute;
    left: 40px; top: 134px;
  }
  .manager-name {
    color: var(--brand-blue);
    font-weight: 700;
    font-size: 17px;
    text-transform: uppercase;
  }
  .manager-role { font-size: 12.5px; color: var(--ink); margin-top: 1px; }
  .contacts {
    position: absolute;
    left: 40px; top: 188px;
    list-style: none;
    font-size: 12px;
    color: var(--ink);
  }
  .contacts li { display: flex; align-items: center; gap: 8px; line-height: 1.55; }
  .contacts svg { width: 11px; height: 11px; fill: var(--brand-blue); }

  /* back */
  .back-band {
    position: absolute;
    left: 0; top: 0; bottom: 0;
    width: 130px;
    background: var(--brand-blue);
    display: flex; align-items: center; justify-content: center;
  }
  .back-brand {
    transform: rotate(-90deg);
    white-space: nowrap;
    display: flex; align-items: center; gap: 10px;
    color: var(--paper);
  }
  .back-brand .brand-square { background: transparent; border: 3px solid var(--paper); width: 34px; height: 34px; }
  .back-brand .brand-name { color: var(--paper); font-size: 28px; }
  .notes-area {
    position: absolute;
    left: 130px; right: 0; top: 0; bottom: 0;
  }
</style>
</head>
<body>
  <section class="card card-front" aria-label="Card front">
    <div class="front-tab"></div>
    <div class="front-brand">
      <div class="brand-square"></div>
      <div class="brand-name">Harborview<span class="brand-sub">Estates LLC</span></div>
    </div>

    <div class="address">
      2760 Larkspur Bay Road #B210<br>
      Oceanside, CA 92054<br>
      <span class="web">www.harborviewestates.us</span>
    </div>

    <div class="manager">
      <div class="manager-name">Daniel Whitmore</div>
      <div class="manager-role">Property Manager</div>
    </div>
    <div class="rule"></div>

    <ul class="contacts">
      <li><svg viewBox="0 0 24 24"><path d="M6.6 10.8a15 15 0 0 0 6.6 6.6l2.2-2.2a1 1 0 0 1 1-.25 11.4 11.4 0 0 0 3.6.57 1 1 0 0 1 1 1V20a1 1 0 0 1-1 1A17 17 0 0 1 3 4a1 1 0 0 1 1-1h3.5a1 1 0 0 1 1 1c0 1.25.2 2.45.57 3.57a1 1 0 0 1-.25 1z"/></svg>555-201-7340</li>
      <li><svg viewBox="0 0 24 24"><path d="M6 3h12v5H6zM3 9h18v9h-3v3H6v-3H3zM8 15v4h8v-4z"/></svg>555-204-9186</li>
      <li><svg viewBox="0 0 24 24"><path d="M2 5h20v14H2zM4 7v.5l8 5 8-5V7z"/></svg>daniel@harborviewestates.us</li>
    </ul>
  </section>

  <section class="card card-back" aria-label="Card back">
    <div class="back-band">
      <div class="back-brand">
        <div class="brand-square"></div>
        <div class="brand-name">Harborview<span class="brand-sub">Estates LLC</span></div>
      </div>
    </div>
    <div class="notes-area"></div>
  </section>
</body>
</html>
```